Flyer for customer acquisition.

Hello, We are a sportmanagement agency from Germany and we need information flyers for customer acquisition. It should be DinA4 and should have a modern but serious design. I have uploaded a information sheet, where you can find the text and the composition, the flyer should have. I also uploaded Pictures / Images, which you can use. Of course you can use other suitable images. If they are not free, I will buy them later. On the bottom of the flyer there has been the contact information. You will find them in the download section, too. If you have questions, just write me. If I forgot something, I will update the letter :) Thank you very much!
Ich brauche zusätzliche Tage um durchzusehen

```html
<!DOCTYPE html>
<html lang="de">
<head>
<meta charset="utf-8">
<title>NOVA-S Nachwuchsförderung – Flyer</title>
<link rel="stylesheet" href="https://fonts.googleapis.com/css2?family=Michroma&family=Montserrat:wght@700;800&family=Open+Sans:wght@400;700&display=swap">
<style>
  :root{
    --page:#e4e4e4;
    --navy:#08111c;
    --navy-2:#0d1c2c;
    --blue:#2a9fd8;
    --blue-deep:#1672a8;
    --orange:#f27a1a;
    --white:#ffffff;
    --muted:#c9d3dc;
    --footer:#0a0a0c;
  }
  *{box-sizing:border-box;margin:0;padding:0}
  html,body{width:707px;height:1200px;overflow:hidden;background:var(--page)}
  .flyer{
    position:absolute;left:0;top:102px;width:707px;height:995px;overflow:hidden;
    background:radial-gradient(ellipse at 50% 75%, #10314a 0%, var(--navy-2) 45%, var(--navy) 80%);
    font-family:"Open Sans",Arial,sans-serif;color:var(--white);
  }
  .hero-photo{
    position:absolute;left:0;top:0;width:707px;height:360px;
    background:
      radial-gradient(ellipse 140px 60px at 80px 40px, rgba(220,235,255,.75), transparent 70%),
      radial-gradient(ellipse 140px 60px at 360px 30px, rgba(200,225,255,.55), transparent 70%),
      radial-gradient(ellipse 120px 50px at 620px 90px, rgba(200,225,255,.5), transparent 70%),
      radial-gradient(ellipse 260px 110px at 360px 290px, rgba(60,170,210,.45), transparent 75%),
      linear-gradient(180deg, #2a4a72 0%, #18304e 40%, #0f2238 70%, var(--navy-2) 100%);
  }
  .hero-photo::after{
    content:"";position:absolute;left:0;right:0;bottom:0;height:120px;
    background:linear-gradient(180deg, transparent, var(--navy-2));
  }
  .brand-pennant{
    position:absolute;left:520px;top:0;width:102px;height:166px;
    display:flex;flex-direction:column;align-items:center;justify-content:center;gap:8px;
  }
  .brand-pennant svg{position:absolute;inset:0}
  .brand-pennant .mark{position:relative;width:22px;height:22px;border-radius:50%;background:var(--white);margin-top:-20px}
  .brand-pennant .name{position:relative;font-family:"Montserrat",sans-serif;font-weight:700;font-size:17px;letter-spacing:1px}
  .title{
    position:absolute;left:0;right:0;top:318px;text-align:center;
    font-family:"Montserrat",sans-serif;font-weight:800;font-size:76px;letter-spacing:2px;line-height:1;
  }
  .subtitle{
    position:absolute;left:0;right:0;top:412px;text-align:center;
    font-family:"Michroma",sans-serif;font-size:33px;line-height:1;color:var(--blue);
    text-shadow:0 0 2px #06203a,1px 1px 0 #06203a;
  }
  .rule{position:absolute;left:0;right:0;top:474px;height:2px;background:var(--muted);opacity:.85}
  .claim{position:absolute;left:0;right:0;text-align:center;font-family:"Michroma",sans-serif;line-height:1}
  .claim-strong{top:487px;font-size:30px;color:var(--orange);letter-spacing:1px}
  .claim-light{top:534px;font-size:25px;color:var(--white);font-weight:400}
  .services{
    position:absolute;left:27px;top:594px;width:659px;
    display:grid;grid-template-columns:repeat(3,192px);column-gap:41px;row-gap:14px;
  }
  .service{
    height:148px;padding:4px 8px 6px;text-align:center;
    background:linear-gradient(180deg, rgba(8,17,28,.6) 0%, rgba(20,80,125,.75) 60%, var(--blue-deep) 100%);
  }
  .service-icon{display:block;width:30px;height:30px;margin:0 auto 3px;background:var(--orange)}
  .service-title{font-size:10.5px;font-weight:700;color:var(--orange);line-height:1.2;margin-bottom:2px}
  .service-text{font-size:9.6px;line-height:1.32}
  .service-text strong{font-weight:700}
  .footnote{
    position:absolute;left:24px;right:24px;top:912px;text-align:center;
    font-size:8.2px;line-height:1.3;color:var(--muted);
  }
  .contact-bar{
    position:absolute;left:0;right:0;bottom:0;height:33px;background:var(--footer);
    display:flex;align-items:center;justify-content:center;gap:14px;
    font-size:15px;font-weight:700;
  }
  .contact-item{display:flex;align-items:center;gap:6px}
  .contact-phone{font-size:18px}
  .divider{width:1px;height:16px;background:var(--muted)}
</style>
</head>
<body>
<main class="flyer">
  <div class="hero-photo" role="img" aria-label="Nachwuchsfußballer mit Ball von hinten im beleuchteten Stadion bei Nacht"></div>

  <div class="brand-pennant">
    <svg width="102" height="166" viewBox="0 0 102 166" aria-hidden="true">
      <path d="M0 0H102V166L51 138L0 166Z" fill="#050608" stroke="#d8d8d8" stroke-width="1.5"/>
    </svg>
    <span class="mark"></span>
    <span class="name">NOVA</span>
  </div>

  <h1 class="title">NOVA-S</h1>
  <p class="subtitle">NACHWUCHSFÖRDERUNG</p>
  <div class="rule"></div>
  <p class="claim claim-strong">WIR BEGLEITEN DICH</p>
  <p class="claim claim-light">AUF DEINEM WEG ZUM PROFI</p>

  <section class="services">
    <article class="service">
      <svg class="service-icon" viewBox="0 0 30 30" aria-hidden="true"><rect width="30" height="30" fill="#f27a1a"/><path d="M7 22V8M7 22H23M10 19l4-5 3 3 5-7" stroke="#fff" stroke-width="1.6" fill="none"/></svg>
      <h2 class="service-title">Karriereplanung</h2>
      <p class="service-text"><strong>Wir haben deine Karriere im Blick!</strong> In enger Absprache mit deinen Eltern und dir leiten wir die richtigen Maßnahmen und Schritte ein, um dein Ziel „Profifußballer“ zu realisieren</p>
    </article>
    <article class="service">
      <svg class="service-icon" viewBox="0 0 30 30" aria-hidden="true"><rect width="30" height="30" fill="#f27a1a"/><rect x="8" y="6" width="14" height="18" stroke="#fff" stroke-width="1.5" fill="none"/><circle cx="15" cy="13" r="3" stroke="#fff" stroke-width="1.5" fill="none"/><path d="M10 22c1-4 9-4 10 0" stroke="#fff" stroke-width="1.5" fill="none"/></svg>
      <h2 class="service-title">Ständiger<br>Ansprechpartner</h2>
      <p class="service-text">Egal um welchen Themen es sich handelt, <strong>wir sind für dich da!</strong> Ein vertrauensvolles und freundschaftliches Verhältnis ist uns besonders wichtig.</p>
    </article>
    <article class="service">
      <svg class="service-icon" viewBox="0 0 30 30" aria-hidden="true"><rect width="30" height="30" fill="#f27a1a"/><path d="M15 6V23M9 23H21M8 10H22M8 10l-3 7h6zM22 10l-3 7h6z" stroke="#fff" stroke-width="1.5" fill="none"/></svg>
      <h2 class="service-title">Rechtsberatung/<br>Vertragsrecht</h2>
      <p class="service-text">Juristendeutsch und Kleingedrucktes? Kein Problem! <strong>Wir helfen dir den Durchblick zu behalten</strong> und holen immer das Beste für dich raus.</p>
    </article>
    <article class="service">
      <svg class="service-icon" viewBox="0 0 30 30" aria-hidden="true"><rect width="30" height="30" fill="#f27a1a"/><circle cx="15" cy="15" r="8" stroke="#fff" stroke-width="1.6" fill="none"/><circle cx="15" cy="15" r="2.8" fill="#fff"/></svg>
      <h2 class="service-title">Ausrüstung</h2>
      <p class="service-text"><strong>Wir besorgen dir deine Ausrüstung!</strong> Unsere Beziehungen zu den großen Sportartikelherstellern ermöglichen den Abschluss von Ausrüsterverträgen*.</p>
    </article>
    <article class="service">
      <svg class="service-icon" viewBox="0 0 30 30" aria-hidden="true"><rect width="30" height="30" fill="#f27a1a"/><path d="M15 7l6 3v5c0 4-3 7-6 8-3-1-6-4-6-8v-5z" stroke="#fff" stroke-width="1.6" fill="none"/><path d="M12 15l2 2 4-4" stroke="#fff" stroke-width="1.6" fill="none"/></svg>
      <h2 class="service-title">Vorsorge</h2>
      <p class="service-text">Verletzungen gehören leider zum Fußball dazu. <strong>Wir sichern dich ab,</strong> indem wir eine private Zusatzkrankenversicherung für dich abschließen.</p>
    </article>
    <article class="service">
      <svg class="service-icon" viewBox="0 0 30 30" aria-hidden="true"><rect width="30" height="30" fill="#f27a1a"/><path d="M15 15L8 9M15 15L22 9M15 15V23" stroke="#fff" stroke-width="1.5"/><circle cx="15" cy="15" r="2.5" fill="#fff"/><circle cx="8" cy="9" r="2.2" fill="#fff"/><circle cx="22" cy="9" r="2.2" fill="#fff"/><circle cx="15" cy="23" r="2.2" fill="#fff"/></svg>
      <h2 class="service-title">Kooperationspartner/netzwerk</h2>
      <p class="service-text">Ob Entscheidungsträger oder Experte, <strong>wir kennen die richtigen Leute.</strong> Zusätzlich bieten wir dir eine große Bandbreite an Leistungen, die du jederzeit in Anspruch nehmen kannst**.</p>
    </article>
  </section>

  <p class="footnote">*Die Entscheidung über das Zustandekommen eines Ausrüstervertrags obliegt dem jeweiligen Sportartikelhersteller. Ist ein Abschluss aktuell nicht möglich, erhältst du von uns 2x pro Saison neue Fußballschuhe sowie weitere Ausrüstungsgegenstände.<br>**Personal Training, Athletik-Training, Ernährungsberatung, Sportpsychologische Betreuung, uvm.</p>

  <footer class="contact-bar">
    <span class="contact-item">
      <svg width="15" height="15" viewBox="0 0 16 16" aria-hidden="true"><circle cx="8" cy="8" r="7.5" fill="#2a9fd8"/><rect x="4" y="5.5" width="8" height="5.5" fill="none" stroke="#0a0a0c" stroke-width="1.1"/><path d="M4 5.5l4 3 4-3" fill="none" stroke="#0a0a0c" stroke-width="1.1"/></svg>
      info@nova-s.de
    </span>
    <span class="divider"></span>
    <span class="contact-item">
      <svg width="15" height="15" viewBox="0 0 16 16" aria-hidden="true"><circle cx="8" cy="8" r="7.5" fill="#2a9fd8"/><circle cx="8" cy="8" r="4" fill="none" stroke="#0a0a0c" stroke-width="1.1"/><path d="M4 8H12M8 4c-2 2.5-2 5.5 0 8M8 4c2 2.5 2 5.5 0 8" fill="none" stroke="#0a0a0c" stroke-width="1"/></svg>
      www.nova-s.de
    </span>
    <span class="divider"></span>
    <span class="contact-item contact-phone">
      <svg width="18" height="18" viewBox="0 0 18 18" aria-hidden="true"><path d="M4 2l3 3-1.5 2c1 2 3 4 5 5L12.5 10.5l3 3-2 2C8 15 3 10 2.5 4z" fill="#2a9fd8"/><path d="M11 3a5 5 0 0 1 4 4M11 5.5a2.5 2.5 0 0 1 1.6 1.6" stroke="#2a9fd8" stroke-width="1.2" fill="none"/></svg>
      07000/4821730
    </span>
  </footer>
</main>
</body>
</html>
```